Business cards for veterinary clinic

Hi, We are looking for business cards to be designed for our other veterinary clinic. We were very happy with the design done for our other clinic a few months ago. We already have a logo for use which I will attach (please use the image not the text around.
We need a couple of different cards (same design with different names on them) produced

Industry/Entity Type

Veterinary

Contact Information for Business Card

Bellwood Creek Vet Clinic
47 Orchard Rd
Kangaroo Flat
VIC 3555
03) 5182 6390
clinic@bellwoodcreekvetclinic.com.au

Font styles to use
Sans Serif

Colors
0455a3
0592cd

Requirements
Must have
• Three different names
• 1. Generic (no name) with email clinic@bellwoodcreekvetclinic.com.au
• 2. Hollis Varne -Director with email hollis@bellwoodcreekvetclinic.com.au
• 3. Dorian Pike - Vet Director with email hollis@bellwoodcreekvetclinic.com.au

```html
<!DOCTYPE html>
<html lang="en">
<head>
<meta charset="utf-8">
<title>Bellwood Creek Vet Clinic – Business Cards</title>
<link rel="stylesheet" href="https://fonts.googleapis.com/css2?family=Lato:wght@300;400;700&display=swap">
<style>
  :root {
    --backdrop: #2b2b2b;
    --brand-deep: #0455a3;
    --brand-sky: #0592cd;
    --card-blue: #1a6fae;
    --card-blue-light: #2d86c4;
    --card-white: #f6f6f6;
    --ink: #2f2f2f;
    --ink-soft: #555;
    --rule: #6b6b6b;
    --tag-light: #a9cbe6;
  }
  * { box-sizing: border-box; margin: 0; padding: 0; }
  html, body { width: 1200px; height: 997px; overflow: hidden; }
  body {
    background: var(--backdrop);
    font-family: "Lato", Arial, sans-serif;
    position: relative;
  }
  .card {
    position: absolute;
    border-radius: 22px;
    box-shadow: 0 18px 40px rgba(0,0,0,.45);
  }
  /* Back of card */
  .card-back {
    left: 70px; top: 90px; width: 540px; height: 330px;
    background: linear-gradient(160deg, var(--card-blue-light), var(--card-blue));
  }
  .back-mark {
    position: absolute; left: 50%; top: 44%;
    transform: translate(-50%, -50%);
    display: flex; align-items: center; gap: 14px;
    color: #fff; font-weight: 700; font-size: 26px; white-space: nowrap;
  }
  .back-mark .dot {
    width: 26px; height: 26px; border-radius: 50%; background: #fff;
  }
  .tagline {
    position: absolute; left: 0; right: 0; bottom: 38px;
    text-align: center; font-size: 14px; letter-spacing: 1.5px;
    color: var(--tag-light); font-weight: 300;
  }
  .tagline strong { color: #fff; font-weight: 400; }

  /* Front of card */
  .card-front {
    left: 590px; top: 480px; width: 560px; height: 342px;
    background: var(--card-white);
    display: flex; align-items: center;
    padding: 0 24px;
  }
  .front-mark {
    width: 160px; flex: none;
    display: flex; flex-direction: column; align-items: center; gap: 10px;
    color: var(--brand-deep); font-weight: 700; font-size: 17px; text-align: center;
    line-height: 1.25;
  }
  .front-mark .dot {
    width: 22px; height: 22px; border-radius: 50%; background: var(--brand-sky);
  }
  .divider {
    width: 3px; height: 232px; background: var(--rule); margin: 0 20px 0 16px; flex: none;
  }
  .details { flex: 1; color: var(--ink); white-space: nowrap; }
  .person-name {
    font-size: 21px; color: var(--brand-sky); font-weight: 300; letter-spacing: .5px;
  }
  .person-name b { color: var(--brand-deep); font-weight: 400; }
  .person-role { font-size: 12px; color: var(--ink-soft); margin-left: 10px; letter-spacing: 0; }
  .person-email { font-size: 12.5px; font-weight: 700; margin-top: 2px; }
  .clinic-name {
    font-size: 18px; color: var(--brand-sky); font-weight: 300; margin-top: 28px;
  }
  .clinic-name b { color: var(--brand-deep); font-weight: 400; }
  .website { font-size: 13px; font-weight: 700; margin-top: 30px; }
  .contact-list { list-style: none; margin-top: 6px; }
  .contact-list li {
    display: flex; align-items: center; gap: 10px;
    font-size: 13.5px; font-weight: 700; height: 23px;
  }
  .contact-list svg { width: 16px; height: 16px; fill: var(--brand-deep); flex: none; }
</style>
</head>
<body>
  <section class="card card-back" aria-label="Card back">
    <div class="back-mark"><span class="dot"></span>Bellwood Creek Vet Clinic</div>
    <p class="tagline">ALL OF YOUR <strong>VETERINARY NEEDS</strong></p>
  </section>

  <section class="card card-front" aria-label="Card front">
    <div class="front-mark"><span class="dot"></span>Bellwood Creek<br>Vet Clinic</div>
    <div class="divider"></div>
    <div class="details">
      <p class="person-name">DORIAN <b>PIKE</b><span class="person-role">Vet Director</span></p>
      <p class="person-email">hollis@bellwoodcreekvetclinic.com.au</p>
      <p class="clinic-name">Bellwood Creek <b>Veterinary Clinic</b></p>
      <p class="website">bellwoodcreekvetclinic.com.au</p>
      <ul class="contact-list">
        <li>
          <svg viewBox="0 0 16 16" aria-hidden="true"><path d="M3 2h3l1 3-2 1a8 8 0 0 0 5 5l1-2 3 1v3a1 1 0 0 1-1 1A12 12 0 0 1 2 3a1 1 0 0 1 1-1z"/></svg>
          (03) 5182 6390
        </li>
        <li>
          <svg viewBox="0 0 16 16" aria-hidden="true"><path d="M1 3h14v10H1z" fill="none" stroke="#0455a3" stroke-width="1.6"/><path d="M1 3l7 6 7-6" fill="none" stroke="#0455a3" stroke-width="1.6"/></svg>
          clinic@bellwoodcreekvetclinic.com.au
        </li>
        <li>
          <svg viewBox="0 0 16 16" aria-hidden="true"><path d="M8 1l7 7h-2v7H9v-4H7v4H3V8H1z"/></svg>
          47 Orchard Rd Marlow Vale VIC 3912
        </li>
      </ul>
    </div>
  </section>
</body>
</html>
```